Venture Keeper's LanternBook

We need a cover design for a printed paperback book 8.5 inches by 11 inches. The book is a self-driven business planning process for people who wish to start or buy a business, be their own boss, entrepreneurs, small and home-based business owners. We hope for a design that is fun, with a treasure map flavor.

```html
<!DOCTYPE html>
<html lang="en">
<head>
<meta charset="utf-8">
<title>Venture Keeper's LanternBook — Cover</title>
<link rel="stylesheet" href="https://fonts.googleapis.com/css2?family=Anton&family=Montserrat:wght@500&display=swap">
<style>
  :root {
    --page-bg: #ffffff;
    --parchment-light: #ecd9a8;
    --parchment-mid: #d9bd7d;
    --parchment-dark: #b88f4e;
    --title-panel: #3b2414;
    --title-ink: #f4e6c2;
    --author-ink: #4a2e18;
    --trail-ink: #8a3b1e;
  }
  html, body {
    margin: 0;
    padding: 0;
    width: 1200px;
    height: 1200px;
    overflow: hidden;
    background: var(--page-bg);
  }
  .canvas {
    position: relative;
    width: 1200px;
    height: 1200px;
  }
  .cover {
    position: absolute;
    left: 270px;
    top: 173px;
    width: 660px;
    height: 854px;
    overflow: hidden;
    background: var(--parchment-mid);
  }
  .cover-artwork {
    position: absolute;
    inset: 0;
    background:
      radial-gradient(ellipse at 50% 45%, rgba(255,248,225,0.55), rgba(255,248,225,0) 60%),
      radial-gradient(ellipse at 50% 50%, rgba(0,0,0,0) 60%, rgba(90,55,20,0.35) 100%),
      linear-gradient(180deg, var(--parchment-light) 0%, var(--parchment-mid) 55%, var(--parchment-dark) 100%);
  }
  .map-trail {
    position: absolute;
    left: 0;
    top: 0;
    width: 660px;
    height: 854px;
  }
  .title-panel {
    position: absolute;
    left: 112px;
    top: 137px;
    width: 436px;
    height: 410px;
    background: var(--title-panel);
    border-radius: 6px;
    box-shadow: 0 0 0 6px var(--parchment-light), 0 0 0 9px var(--title-panel);
    display: flex;
    align-items: center;
    justify-content: center;
  }
  .book-title {
    margin: 0;
    font-family: "Anton", "Oswald", sans-serif;
    font-weight: 400;
    font-size: 66px;
    line-height: 1.38;
    color: var(--title-ink);
    text-align: center;
    text-transform: uppercase;
  }
  .book-title span { display: block; }
  .author-name {
    position: absolute;
    left: 0;
    right: 0;
    top: 668px;
    margin: 0;
    text-align: center;
    font-family: "Montserrat", sans-serif;
    font-weight: 500;
    font-size: 13px;
    letter-spacing: 0.08em;
    text-transform: uppercase;
    color: var(--author-ink);
  }
</style>
</head>
<body>
  <main class="canvas">
    <section class="cover">
      <div class="cover-artwork" role="img" aria-label="Warm aged parchment background evoking an old treasure map"></div>
      <svg class="map-trail" viewBox="0 0 660 854" aria-hidden="true">
        <path d="M60 60 C 160 20, 260 110, 360 70 S 560 40, 610 110"
              fill="none" stroke="var(--trail-ink)" stroke-width="4" stroke-dasharray="12 10" stroke-linecap="round"/>
        <path d="M50 810 C 140 730, 260 800, 360 760 S 540 720, 600 770"
              fill="none" stroke="var(--trail-ink)" stroke-width="4" stroke-dasharray="12 10" stroke-linecap="round"/>
        <circle cx="60" cy="60" r="8" fill="var(--trail-ink)"/>
        <circle cx="600" cy="770" r="10" fill="none" stroke="var(--trail-ink)" stroke-width="4"/>
      </svg>
      <div class="title-panel">
        <h1 class="book-title">
          <span>Venture</span>
          <span>Keeper's</span>
          <span>LanternBook</span>
        </h1>
      </div>
      <p class="author-name">Lewis Marchand</p>
    </section>
  </main>
</body>
</html>
```